Workers comp/Business Ins/ Payroll- Postcard

I own an insurance agency.  I'm interested in getting some professional advice on how to design a message for what i want to sell.  The products I want to sell are 1) Workers compensation 2) business Insurance 3) Payroll processing. They are integrated together but I'm not sure if it's too much to put on a postcard and if I don't put it on a postcard I could be missing out on sales.
I have the ability to look up what Insurance company a business has their workers compensation  policy with, along with their expiration date.  Based on that information I can tell if the business is overpaying for their Workers compensation. insurance. Most companies are overpaying so I can usually save a company money very quickly if I can get in front of them. Some businesses work with a broker such as myself and buy a policy. When it's done this way, the business ESTIMATES his payroll for the year and at the end of the year they have to complete an audit to find out the actual payroll. Based on audit, they will either owe more money if they were low or get money back if they were high. The other way a business buys a workers comp. policy is with their payroll company. The payroll company will place the policy on Pay -as- you -go which means when you pay your employees every week they  will also calculate how much the workers comp premium is for the week and take that amount out of their checking account. This method avoids large down payments, helps with cash flow and should be very accurate at the end of the policy term.  This is by far the best way to do this for the businessowner. My company also has payroll company and we do this for the insured as well. However, most payroll company's such as KRV and Wagebrook charge the customer $15 every time they do this so if it's weekly it is another $780 a year.  We also complete the insured's audit for them which is a big headache for the businessowner.
One of our biggest benefits of doing business with our company is we have a  Price lock for Life. When you sign up your base price will never increase. Payroll companies are famous for "discounting a new client" only to increase the rate in a few months later. Our service is also superior to the other payroll companies who use overseas service centers. We have staff within our office and we can answer questions quickly. We usually save businesses money on  their Payroll processing but it's not what we focus on- We focus on the Service.
Business Insurance- One of our main companies that we represent is Tolland Insurance. Tolland is very competitive and we usually write business accounts where we save the business owner money but offer superior coverages.
in summary, I'm offering 1) better workers compensation rates 2) Pay as you go workers comp. 3) Price Lock, audits done for you, and superior customer service with our payroll company 4) savings on their business insurance with superior coverages.
Sometimes when we talk to an insured we may start with just their payroll and later get the WC and business liability. Each account is different and we do not pressure people to make decisions and we do what is right for them.  The biggest takeaway is we take some things off the plate for the businessowner where they can make just one phone call to get what they need done.  Our Website is www.brightmoor-partners.net. my email is tomk@brightmoor-partners.net if you have any questions.
Thank You
Tom Kessler

Target Market(s)
Small business owners 1-50 employees
Industry/Entity Type
Insurance and Payroll
Font styles to use
Other font styles liked:
- Let designer choose

Colors
Designer to choose colors to be used in the design.
Requirements
Must have
- It shouldn't be boring- needs to stand out- can use 6x11 inch postcard

Nice to have
- I like humor but not a must

Should not have
- Nothing I can think of

```html
<!DOCTYPE html>
<html lang="en">
<head>
<meta charset="utf-8">
<title>Brightmoor Partners Insurance – Postcard</title>
<link href="https://fonts.googleapis.com/css2?family=Poppins:wght@400;500;600&family=Tinos:wght@700&display=swap" rel="stylesheet">
<style>
:root{
  --stage:#878787;
  --ink:#111111;
  --maroon:#a3393f;
  --maroon-dark:#8e2d33;
  --white:#ffffff;
  --sans:'Poppins', Arial, sans-serif;
  --serif:'Tinos', 'Times New Roman', serif;
}
*{margin:0;padding:0;box-sizing:border-box}
html,body{width:1002px;height:1200px;overflow:hidden;background:var(--stage)}
.postcard{position:absolute;left:75px;width:855px;height:466px;background:var(--white);overflow:hidden;box-shadow:0 14px 16px rgba(0,0,0,.28);font-family:var(--sans);color:var(--ink)}
.postcard--front{top:90px}
.postcard--back{top:642px}

/* top tagline band */
.tagline{position:absolute;left:0;top:0;width:855px;height:33px;background:var(--ink);color:var(--white);font-weight:500;font-size:18px;letter-spacing:5.2px;line-height:33px;text-align:center;white-space:nowrap}
.tagline-tab{position:absolute;left:0;top:0;width:542px;height:33px;background:var(--ink);clip-path:polygon(0 0,100% 0,517px 100%,0 100%)}
.tagline-tab span{position:absolute;left:23px;top:0;line-height:33px;color:var(--white);font-weight:500;font-size:16px;white-space:nowrap}

/* front background */
.front-base{position:absolute;left:0;top:33px;width:855px;height:367px;background:linear-gradient(100deg,#bdbfc1 0%,#f4f4f4 45%,#bfc2c4 70%)}
.front-photo{position:absolute;left:0;top:33px;width:855px;height:367px;background:linear-gradient(160deg,#eef3fa 0%,#d8e2ef 30%,#e9c9b5 55%,#f6f7fb 75%,#53607d 100%);clip-path:polygon(524px 0,855px 0,855px 367px,524px 367px,421px 184px)}
.front-band{position:absolute;left:0;top:33px;width:855px;height:367px;background:linear-gradient(90deg,var(--maroon) 0%,#a6434a 100%);clip-path:polygon(0 184px,421px 184px,524px 367px,0 367px)}

/* brand */
.brand{position:absolute;left:48px;width:280px;text-align:center;color:var(--maroon-dark);font-family:var(--serif);font-weight:700}
.brand-name{font-size:22px;line-height:26px;letter-spacing:.5px;white-space:nowrap}
.brand-sub{font-size:10px;letter-spacing:11px;line-height:12px;margin-top:2px}

/* services */
.service{position:absolute;font-weight:500;font-size:19px;line-height:22px;white-space:nowrap}
.service svg{position:absolute;left:-26px;top:5px}

.headline{position:absolute;left:25px;color:var(--white);font-family:var(--serif);font-weight:700;font-size:38px;line-height:46px;white-space:nowrap}
.pill{position:absolute;left:25px;top:337px;width:318px;height:38px;background:var(--ink);border-radius:5px;color:var(--white);font-weight:500;font-size:13.4px;line-height:38px;text-align:center}
.social{position:absolute;top:348px;width:22px;height:22px;border:2px solid var(--white);border-radius:5px}

/* contact bars */
.contact{position:absolute;left:0;top:400px;width:855px;height:33px;padding:0 22px;display:flex;align-items:center;justify-content:space-between;font-weight:500;font-size:11.6px;white-space:nowrap}
.contact--light{background:linear-gradient(90deg,#f6f6f6,#ffffff 40%,#e6e6e6)}
.contact--red{background:var(--maroon);color:var(--white)}
.contact-item{display:flex;align-items:center;gap:6px;flex:none}
.contact-sep{flex:none;width:1px;height:17px;background:currentColor}
.contact strong{font-weight:500;font-size:13px}
.locations{position:absolute;left:0;top:433px;width:855px;height:33px;background:var(--ink);color:var(--white);font-size:12.2px;line-height:33px;padding-left:23px;white-space:nowrap}

/* back */
.back-photo{position:absolute;left:0;top:33px;width:855px;height:367px;background:radial-gradient(ellipse at 45% 45%,#f0e6e1 0%,rgba(255,255,255,0) 45%),radial-gradient(ellipse at 80% 30%,#e8ecf5 0%,rgba(255,255,255,0) 50%),linear-gradient(90deg,#fbfbfc,#f3f1f2 55%,#fbf4ef)}
.stamp{position:absolute;left:763px;top:29px;width:65px;height:64px;border:1.5px solid var(--ink);border-radius:6px}
.address-line{position:absolute;left:512px;width:310px;height:1px;background:var(--ink)}
.lines-of-business{position:absolute;left:48px;top:142px;width:280px;text-align:center;font-weight:600;font-size:10.6px}
.question{position:absolute;left:46px;font-family:var(--serif);font-weight:700;font-size:28px;line-height:32px;white-space:nowrap}
.question .accent{color:var(--maroon)}
.question-tick{position:absolute;left:18px}
.body-copy{position:absolute;font-size:13.2px;line-height:15.6px}
.offer-band{position:absolute;left:515px;top:206px;width:300px;height:31px;background:var(--maroon);clip-path:polygon(0 0,100% 0,272px 100%,0 100%);color:var(--white);font-family:var(--serif);font-weight:700;font-size:12.6px;line-height:31px;padding-left:22px}
.offer-list{position:absolute;left:515px;top:250px;list-style:none}
.offer-list li{position:relative;padding-left:21px;height:20.6px;font-family:var(--serif);font-weight:700;font-size:12.6px;line-height:16px;white-space:nowrap}
.offer-list li svg{position:absolute;left:0;top:1px}
</style>
</head>
<body>

<section class="postcard postcard--front">
  <div class="tagline">GET BETTER RATES • PAY-AS-YOU-GO • LIFETIME PRICE LOCK</div>
  <div class="front-base"></div>
  <div class="front-photo" role="img" aria-label="Photo of business people's hands reviewing a printed contract with pens"></div>
  <div class="front-band"></div>

  <div class="brand" style="top:86px">
    <div class="brand-name">BRIGHTMOOR PARTNERS</div>
    <div class="brand-sub">INSURANCE</div>
  </div>

  <div class="service" style="left:48px;top:147px">
    <svg width="16" height="12" viewBox="0 0 16 12"><path d="M1 6l4 4 9-9" fill="none" stroke="#a3393f" stroke-width="2.6"/></svg>Workers Comp</div>
  <div class="service" style="left:240px;top:149px">
    <svg width="16" height="12" viewBox="0 0 16 12"><path d="M1 6l4 4 9-9" fill="none" stroke="#a3393f" stroke-width="2.6"/></svg>Business Insurance</div>
  <div class="service" style="left:48px;top:181px">
    <svg width="16" height="12" viewBox="0 0 16 12"><path d="M1 6l4 4 9-9" fill="none" stroke="#a3393f" stroke-width="2.6"/></svg>Payroll Processing</div>

  <div class="headline" style="top:233px">Cut Costs. Save Time.</div>
  <div class="headline" style="top:279px">Simplify Your Business.</div>

  <div class="pill">One Call. One Team. Everything You Need.</div>
  <span class="social" style="left:370px"></span>
  <span class="social" style="left:403px"></span>
  <span class="social" style="left:433px"></span>

  <div class="contact contact--light">
    <div class="contact-item">
      <svg width="14" height="10" viewBox="0 0 14 10"><rect x=".7" y=".7" width="12.6" height="8.6" fill="none" stroke="#a3393f" stroke-width="1.4"/><path d="M1 1l6 5 6-5" fill="none" stroke="#a3393f" stroke-width="1.4"/></svg>
      tomk@brightmoor-partners.net</div>
    <span class="contact-sep"></span>
    <div class="contact-item">
      <svg width="12" height="12" viewBox="0 0 12 12"><path d="M2.5 1l2 2.6-1.2 1.4c.8 1.6 2 2.8 3.6 3.6l1.4-1.2 2.6 2-1.3 1.6C5.5 10.6 1.4 6.5 1 2.3z" fill="#a3393f"/></svg>
      <span>Call us today - <strong>555.201.4400 or (800) 555-0142</strong></span></div>
    <span class="contact-sep"></span>
    <div class="contact-item">
      <svg width="12" height="12" viewBox="0 0 12 12"><path d="M1 1l10 4-4 1.5L5.5 11z" fill="#a3393f"/></svg>
      www.brightmoor-partners.net</div>
  </div>
  <div class="locations">TWO LOCATIONS &nbsp;:&nbsp; 1280 MILL ROAD | MILTON, NY 14000 • 555-201-4400 &nbsp;|&nbsp; 22 OAK PLACE | KENTON, NY 14000 • 555-201-4522</div>
</section>

<section class="postcard postcard--back">
  <div class="back-photo" role="img" aria-label="Faded photo of hands holding a pen and a printed contract"></div>
  <div class="tagline-tab"><span>GET BETTER RATES • PAY-AS-YOU-GO • LIFETIME PRICE LOCK</span></div>

  <div class="stamp"></div>
  <span class="address-line" style="top:135px"></span>
  <span class="address-line" style="top:177px"></span>

  <div class="brand" style="top:95px">
    <div class="brand-name">BRIGHTMOOR PARTNERS</div>
    <div class="brand-sub">INSURANCE</div>
  </div>
  <div class="lines-of-business">AUTO | HOME | BUSINESS | PAYROLL</div>

  <svg class="question-tick" style="top:174px" width="24" height="18" viewBox="0 0 24 18"><path d="M2 9l7 7L22 2" fill="none" stroke="#111" stroke-width="3.4"/></svg>
  <div class="question" style="top:167px">Are You Overpaying</div>
  <div class="question" style="top:199px"><span class="accent">for Workers Comp?</span></div>
  <p class="body-copy" style="left:46px;top:228px;width:345px">We can tell you right now who your policy is with and if you're spending too much. Most companies are - and we fix that fast.</p>

  <svg class="question-tick" style="top:302px" width="24" height="18" viewBox="0 0 24 18"><path d="M2 9l7 7L22 2" fill="none" stroke="#111" stroke-width="3.4"/></svg>
  <div class="question" style="left:47px;top:294px">Business <span class="accent">Insurance?</span></div>
  <p class="body-copy" style="left:47px;top:324px;width:320px">We work with Tolland Insurance and others to save you money without cutting coverage.</p>

  <div class="offer-band">Smart Payroll + Workers Comp Integration</div>
  <ul class="offer-list">
    <li><svg width="12" height="12" viewBox="0 0 12 12"><rect width="12" height="12" fill="#a3393f"/><path d="M2.5 6l2.5 2.5 4.5-5" fill="none" stroke="#fff" stroke-width="1.6"/></svg>Pay-As-You-Go - &nbsp;No Big Down Payments</li>
    <li><svg width="12" height="12" viewBox="0 0 12 12"><rect width="12" height="12" fill="#a3393f"/><path d="M2.5 6l2.5 2.5 4.5-5" fill="none" stroke="#fff" stroke-width="1.6"/></svg>Audit Support - We Handle It For You</li>
    <li><svg width="12" height="12" viewBox="0 0 12 12"><rect width="12" height="12" fill="#a3393f"/><path d="M2.5 6l2.5 2.5 4.5-5" fill="none" stroke="#fff" stroke-width="1.6"/></svg>Price Lock for Life - No Surprise Rate Hikes</li>
    <li><svg width="12" height="12" viewBox="0 0 12 12"><rect width="12" height="12" fill="#a3393f"/><path d="M2.5 6l2.5 2.5 4.5-5" fill="none" stroke="#fff" stroke-width="1.6"/></svg>No Extra Fees - Unlike KRV &amp; Wagebrook</li>
  </ul>
  <p class="body-copy" style="left:515px;top:337px;width:320px">Bonus: Our U.S.-based team offers real, responsive service —no overseas call centers.</p>

  <p class="body-copy" style="left:47px;top:375px;white-space:nowrap">Let’s Make It Easy. Whether you start with payroll, workers comp, or insurance—we’ll handle it. You focus on your business.</p>

  <div class="contact contact--red">
    <div class="contact-item">
      <svg width="14" height="10" viewBox="0 0 14 10"><rect x=".7" y=".7" width="12.6" height="8.6" fill="none" stroke="#fff" stroke-width="1.4"/><path d="M1 1l6 5 6-5" fill="none" stroke="#fff" stroke-width="1.4"/></svg>
      tomk@brightmoor-partners.net</div>
    <span class="contact-sep"></span>
    <div class="contact-item">
      <svg width="12" height="12" viewBox="0 0 12 12"><path d="M2.5 1l2 2.6-1.2 1.4c.8 1.6 2 2.8 3.6 3.6l1.4-1.2 2.6 2-1.3 1.6C5.5 10.6 1.4 6.5 1 2.3z" fill="#fff"/></svg>
      <span>Call us today - <strong>555.201.4400 or (800) 555-0142</strong></span></div>
    <span class="contact-sep"></span>
    <div class="contact-item">
      <svg width="12" height="12" viewBox="0 0 12 12"><path d="M1 1l10 4-4 1.5L5.5 11z" fill="#fff"/></svg>
      www.brightmoor-partners.net</div>
  </div>
  <div class="locations">TWO LOCATIONS &nbsp;:&nbsp; 1280 MILL ROAD | MILTON, NY 14000 • 555-201-4400 &nbsp;|&nbsp; 22 OAK PLACE | KENTON, NY 14000 • 555-201-4522</div>
</section>

</body>
</html>
```